Create Social Media design templates for Online-Education-Startup

We are an online platform for pupils who provide group courses and on demand individual tutroing lessons. Our core values are personalisation, family and success. We need a holistic social media design concept which includes nine possible layouts for Instagram posts which reflect our values and promote not only our offerings and special deals but also support in building our brand image (for example: telling company history, daily news, funny facts, getting to know the team etc.).
Additionally, we need design elements for our YouTube channel:
-Videocover
-Cover Image for the channel

Our main colour is orange (RGB-Code: 255;105;31) and additional colours white, black, and grey. For the reference have a look at our website: www.lernvolta.de.

Target Market(s)

We want to attract customers to our online tutoring courses and build a brand.

Industry/Entity Type

Education / Tutoring

Font styles to use
Sans Serif

Requirements
Must have
• Familiarize yourself with the style of our website. The designs should fit as well as possible.

```html
<!DOCTYPE html>
<html lang="en">
<head>
<meta charset="utf-8">
<title>Lernvolta – Online Tutoring Post</title>
<link rel="stylesheet" href="https://fonts.googleapis.com/css2?family=Poppins:ital,wght@0,300;0,400;0,500;0,700;0,800;1,800&display=swap">
<style>
  :root {
    --orange: #ec6a2c;
    --black: #0b0b0b;
    --white: #ffffff;
    --badge-dark: #1c1b1c;
    --badge-light: #3a3839;
    --photo-a: #6d6a6b;
    --photo-b: #b8b4b2;
    --photo-c: #2c2f4a;
  }
  html, body {
    margin: 0;
    padding: 0;
    width: 1200px;
    height: 1200px;
    overflow: hidden;
    background: var(--white);
  }
  .post {
    position: relative;
    width: 1200px;
    height: 1200px;
    overflow: hidden;
    font-family: "Poppins", sans-serif;
    color: var(--black);
  }
  .post-shapes {
    position: absolute;
    inset: 0;
  }
  .brand {
    position: absolute;
    left: 92px;
    top: 54px;
    display: flex;
    align-items: center;
    gap: 20px;
  }
  .brand-dot {
    width: 112px;
    height: 112px;
    border-radius: 50%;
    background: var(--orange);
  }
  .brand-text { line-height: 1.2; }
  .brand-name {
    font-size: 34px;
    font-weight: 700;
    color: var(--black);
  }
  .brand-sub {
    font-size: 33px;
    font-weight: 400;
    color: var(--black);
  }
  .headline {
    position: absolute;
    left: 76px;
    top: 732px;
    margin: 0;
    font-size: 70px;
    font-weight: 800;
    font-style: italic;
    line-height: 72px;
    letter-spacing: -1px;
  }
  .headline .accent { color: var(--orange); display: block; }
  .headline .lead { display: block; }
  .slogan {
    position: absolute;
    left: 84px;
    top: 908px;
    margin: 0;
    font-size: 40px;
    font-weight: 400;
  }
  .values {
    position: absolute;
    left: 71px;
    top: 971px;
    height: 57px;
    display: flex;
  }
  .value {
    height: 57px;
    line-height: 57px;
    font-size: 36px;
    font-weight: 300;
    color: var(--white);
    padding: 0 26px 0 14px;
    clip-path: polygon(0 0, calc(100% - 16px) 0, 100% 100%, 0 100%);
  }
  .value + .value {
    margin-left: -16px;
    padding-left: 28px;
    clip-path: polygon(0 0, calc(100% - 16px) 0, 100% 100%, 16px 100%);
  }
  .value-orange { background: var(--orange); }
  .value-black { background: var(--black); }
  .offer-badge {
    position: absolute;
    left: 787px;
    top: 701px;
    width: 358px;
    height: 358px;
    text-align: center;
  }
  .offer-badge svg { position: absolute; inset: 0; }
  .offer-text {
    position: absolute;
    inset: 0;
    display: flex;
    flex-direction: column;
    align-items: center;
    justify-content: center;
    font-weight: 700;
    line-height: 1;
  }
  .offer-free {
    color: var(--orange);
    font-size: 104px;
    letter-spacing: -3px;
    margin-bottom: 6px;
  }
  .offer-line {
    color: var(--white);
    font-size: 60px;
    letter-spacing: -1px;
    line-height: 58px;
  }
  .call {
    position: absolute;
    left: 56px;
    top: 1112px;
    display: flex;
    align-items: center;
    color: var(--white);
    font-weight: 700;
  }
  .call-label { font-size: 47px; letter-spacing: -0.5px; }
  .call-icon { margin: 0 12px 0 20px; }
  .call-number { font-size: 52px; letter-spacing: -0.5px; }
  .contact {
    position: absolute;
    left: 838px;
    top: 1102px;
    list-style: none;
    margin: 0;
    padding: 0;
    color: var(--white);
    font-size: 23px;
    font-weight: 400;
  }
  .contact li {
    display: flex;
    align-items: center;
    gap: 12px;
    height: 38px;
  }
</style>
</head>
<body>
<main class="post">
  <svg class="post-shapes" width="1200" height="1200" viewBox="0 0 1200 1200">
    <defs>
      <linearGradient id="photoTone" x1="0" y1="0" x2="1" y2="0.4">
        <stop offset="0" stop-color="var(--photo-c)"/>
        <stop offset="0.35" stop-color="var(--photo-a)"/>
        <stop offset="1" stop-color="var(--photo-b)"/>
      </linearGradient>
    </defs>
    <rect class="hero-photo" x="0" y="0" width="1200" height="720" fill="url(#photoTone)" role="img" aria-label="Photo of a smiling girl at a desk taking an online lesson with a tutor on a laptop"/>
    <!-- header swoosh -->
    <path class="header-band" d="M0,148 L0,200 C170,250 440,250 712,0 L690,0 C500,210 250,230 0,148 Z" fill="var(--orange)"/>
    <path class="header-field" d="M0,0 H686 C500,190 250,215 0,145 Z" fill="var(--white)"/>
    <!-- lower swoosh -->
    <path class="wave-black" d="M0,505 C220,620 480,680 760,700 L0,700 Z" fill="var(--black)"/>
    <path class="wave-line" d="M0,496 C300,640 800,690 1200,500" fill="none" stroke="var(--white)" stroke-width="6"/>
    <path class="wave-orange" d="M120,570 C450,690 850,680 1200,520 L1200,592 C850,700 450,710 120,600 Z" fill="var(--orange)"/>
    <path class="wave-black-right" d="M1200,596 L1200,626 C1100,650 1000,670 900,684 C1000,660 1110,630 1200,596 Z" fill="var(--black)"/>
    <path class="content-field" d="M0,700 C20,640 80,600 170,612 C420,650 760,700 1200,628 V1200 H0 Z" fill="var(--white)"/>
    <!-- footer -->
    <path class="footer-black" d="M0,1085 H762 L812,1200 H0 Z" fill="var(--black)"/>
    <path class="footer-orange" d="M772,1085 H1200 V1200 H826 Z" fill="var(--orange)"/>
    <path class="call-strip" d="M0,1104 H386 L400,1184 H0 Z" fill="var(--orange)"/>
  </svg>

  <div class="brand">
    <div class="brand-dot"></div>
    <div class="brand-text">
      <div class="brand-name">Lernvolta</div>
      <div class="brand-sub">Bildungsinstitut</div>
    </div>
  </div>

  <h1 class="headline">
    <span class="lead">ONLINE TUTORING</span>
    <span class="accent">AT LERNVOLTA</span>
  </h1>

  <p class="slogan">Together for your degree!</p>

  <div class="values">
    <span class="value value-orange">Personal.</span>
    <span class="value value-black">Family.</span>
    <span class="value value-orange">Successful.</span>
  </div>

  <div class="offer-badge">
    <svg width="358" height="358" viewBox="0 0 358 358">
      <defs>
        <clipPath id="badgeClip"><circle cx="179" cy="179" r="179"/></clipPath>
      </defs>
      <circle cx="179" cy="179" r="179" fill="var(--black)"/>
      <g clip-path="url(#badgeClip)">
        <circle cx="179" cy="179" r="170" fill="var(--badge-dark)"/>
        <path d="M20,0 H358 V330 Z" fill="var(--badge-light)" opacity="0.7"/>
      </g>
      <circle cx="179" cy="179" r="162" fill="none" stroke="var(--white)" stroke-width="2.5" stroke-dasharray="1 6" stroke-linecap="round"/>
    </svg>
    <div class="offer-text">
      <span class="offer-free">FREE</span>
      <span class="offer-line">TRIAL</span>
      <span class="offer-line">LESSON</span>
    </div>
  </div>

  <div class="call">
    <span class="call-label">CALL NOW</span>
    <svg class="call-icon" width="50" height="50" viewBox="0 0 50 50" aria-hidden="true">
      <circle cx="25" cy="25" r="23" fill="var(--white)"/>
      <circle cx="25" cy="25" r="17" fill="none" stroke="var(--orange)" stroke-width="3"/>
      <path d="M18,14 l5,0 l2,7 l-3,2 c1.5,3 3.5,5 6.5,6.5 l2,-3 l7,2 l0,5 c-12,1 -20,-7 -19.5,-19.5 Z" fill="var(--black)"/>
    </svg>
    <span class="call-number">089 55501234</span>
  </div>

  <ul class="contact">
    <li>
      <svg width="24" height="24" viewBox="0 0 24 24" aria-hidden="true" fill="none" stroke="var(--white)" stroke-width="1.6">
        <circle cx="12" cy="12" r="10"/>
        <ellipse cx="12" cy="12" rx="4.5" ry="10"/>
        <path d="M2,12 H22 M4,6.5 H20 M4,17.5 H20"/>
      </svg>
      www.lernvolta.de
    </li>
    <li>
      <svg width="24" height="24" viewBox="0 0 24 24" aria-hidden="true">
        <rect x="1" y="5" width="22" height="14" fill="var(--white)"/>
        <path d="M1,5 L12,13 L23,5" fill="none" stroke="var(--orange)" stroke-width="1.8"/>
      </svg>
      kontakt@lernvolta.de
    </li>
  </ul>
</main>
</body>
</html>
```